Fast-casual chicken restaurant Crisp Harbor needs a catering menu design

We need a catering menu designed for Crisp Harbor. We are looking to design a 24x36in landscape menu board for our new catering menu. The catering memo attached includes our catering menu and Crisp Harbor branding. More information about our brand can be found at https://crispharbor-eats.example/.

```html
<!DOCTYPE html>
<html lang="en">
<head>
<meta charset="utf-8">
<title>Crisp Harbor Catering Menu</title>
<link rel="stylesheet" href="https://fonts.googleapis.com/css2?family=Montserrat:wght@400;500;600;700;800;900&display=swap">
<style>
:root{
  --yellow:#fccb2d;
  --red:#d53f2d;
  --white:#ffffff;
  --navy:#2d3c5e;
  --wood:#8a5a32;
  --wood-dark:#5a3619;
  --food-warm:#c9652a;
  --food-gold:#d9a24c;
}
*{margin:0;padding:0;box-sizing:border-box}
html,body{width:1200px;height:800px;overflow:hidden}
body{font-family:"Montserrat",sans-serif;background:var(--wood)}
.menu-board{position:relative;width:1200px;height:800px;overflow:hidden;
  background:linear-gradient(180deg,var(--wood) 0%,#9b6a3d 50%,var(--wood) 100%)}
.photo{position:absolute}
.photo-top-left{left:0;top:0;width:330px;height:160px;border-radius:0 0 160px 0;background:radial-gradient(ellipse at 40% 40%,var(--food-gold),var(--food-warm) 70%,#7a3d1c)}
.photo-top-right{right:0;top:0;width:330px;height:160px;border-radius:0 0 0 160px;background:radial-gradient(ellipse at 60% 40%,var(--food-gold),var(--food-warm) 70%,#7a3d1c)}
.photo-ribs-left{left:330px;top:0;width:150px;height:80px;border-radius:0 0 50px 50px;background:radial-gradient(ellipse,#6e2a16,#2a1a14)}
.photo-ribs-right{left:720px;top:0;width:150px;height:80px;border-radius:0 0 50px 50px;background:radial-gradient(ellipse,#6e2a16,#2a1a14)}
.photo-bottom{left:0;bottom:0;width:1200px;height:110px;background:linear-gradient(90deg,#3a2419,#b0481f 15%,#d9a24c 35%,#c9652a 50%,#d9a24c 65%,#b0481f 85%,#3a2419)}
.panel{position:absolute;left:72px;top:124px;width:1056px;height:576px;background:var(--yellow)}
.photo-platter{left:488px;top:0;width:224px;height:184px;border-radius:0 0 14px 14px;background:radial-gradient(ellipse at 50% 45%,#9a3a18,var(--food-warm) 40%,var(--food-gold) 75%,#efe8df 95%)}
.photo-side-left{left:0;top:600px;width:150px;height:110px;border-radius:0 40px 0 0;background:radial-gradient(ellipse,#7a2e18,#2a1a14)}
.photo-side-right{right:0;top:600px;width:150px;height:110px;border-radius:40px 0 0 0;background:radial-gradient(ellipse,#7a2e18,#2a1a14)}
.photo-hands{left:340px;top:684px;width:520px;height:116px;border-radius:60px 60px 0 0;background:linear-gradient(90deg,#d9a24c,#f1d6c2 30%,#f1d6c2 70%,#d9a24c)}

.title{position:absolute;left:0;width:1200px;top:188px;text-align:center;color:var(--red);font-weight:800;font-size:80px;letter-spacing:5px;line-height:1}
.section-head{position:absolute;color:var(--white);font-weight:800;font-size:23px;letter-spacing:2.5px;line-height:1;display:flex;align-items:center;gap:12px}
.section-head::after{content:"";flex:1;height:3px;background:var(--white)}
.head-per-person{left:130px;top:269px;width:484px}
.head-package{left:670px;top:269px;width:412px}
.head-own{left:130px;top:521px;width:952px}
.note{position:absolute;left:130px;top:291px;font-size:8.5px;font-weight:700;font-style:italic;color:var(--navy);letter-spacing:.3px}

.option{position:absolute;top:310px;width:150px;height:190px;
  background:linear-gradient(90deg,rgba(0,0,0,.06),rgba(0,0,0,0) 40%);
  clip-path:polygon(0 0,100% 0,100% 100%,0 100%,0 30%,14px 22%,0 14%)}
.option-label{position:absolute;top:333px;font-size:9.5px;letter-spacing:1.5px;color:var(--red);font-weight:500}
.option-name{position:absolute;top:343px;font-size:23px;font-weight:800;color:var(--red);letter-spacing:.3px}
.option-items{position:absolute;top:380px;font-size:13.5px;line-height:14px;color:var(--red);font-weight:500;text-transform:uppercase}
.option-price{position:absolute;top:481px;font-size:12px;letter-spacing:1.8px;color:var(--red);font-weight:500}

.package{position:absolute;top:294px;width:129px;height:215px;background:var(--red);border-radius:0 0 6px 6px;color:var(--white);text-align:center}
.package-head{height:58px;background:var(--white);color:var(--red);font-weight:800;font-size:21px;line-height:20px;display:flex;align-items:center;justify-content:center;position:relative}
.package-head::after{content:"";position:absolute;left:50%;bottom:-10px;margin-left:-11px;border-left:11px solid transparent;border-right:11px solid transparent;border-top:10px solid var(--white)}
.package-items{position:absolute;left:0;right:0;font-size:12.5px;line-height:14px;font-weight:500}
.package-price{position:absolute;left:0;right:0;top:182px;font-size:12px;letter-spacing:1.5px;font-weight:500}

.count-box{position:absolute;top:550px;height:92px;background:var(--red);border-radius:4px;color:var(--white)}
.count-box h3{position:absolute;top:3px;font-size:20px;font-weight:800;font-style:italic;letter-spacing:.5px}
.count{position:absolute;font-size:11.5px;line-height:12px;font-weight:600;letter-spacing:1px}
.item{position:absolute;top:554px;color:var(--red)}
.item h3{font-size:20px;font-weight:800;line-height:20px}
.item p{font-size:11.5px;font-weight:500;margin-top:2px;line-height:12px;letter-spacing:.3px}
.item .price{letter-spacing:1px}

.learn-more{position:absolute;right:168px;top:651px;height:22px;border:1.5px solid var(--navy);border-radius:3px;background:var(--white);color:var(--navy);font-size:11.5px;line-height:19px;padding:0 6px;letter-spacing:.2px;font-weight:500;white-space:nowrap}
.learn-more b{font-weight:800}
.cursor{position:absolute;left:1030px;top:652px}
</style>
</head>
<body>
<div class="menu-board">
  <div class="photo photo-top-left" role="img" aria-label="Platter of assorted chicken wings"></div>
  <div class="photo photo-top-right" role="img" aria-label="Platter of assorted chicken wings"></div>
  <div class="photo photo-ribs-left" role="img" aria-label="Tray of barbecue ribs"></div>
  <div class="photo photo-ribs-right" role="img" aria-label="Tray of barbecue ribs"></div>
  <div class="photo photo-bottom" role="img" aria-label="Platters of sauced tenders, wings and waffle fries on a wooden table"></div>

  <div class="panel"></div>

  <div class="photo photo-platter" role="img" aria-label="Platter of crispy chicken tenders"></div>
  <div class="photo photo-side-left" role="img" aria-label="Tray of barbecue ribs"></div>
  <div class="photo photo-side-right" role="img" aria-label="Tray of barbecue ribs"></div>
  <div class="photo photo-hands" role="img" aria-label="Hands dipping chicken tenders into sauce over plates"></div>

  <h1 class="title">CATERING MENU</h1>

  <h2 class="section-head head-per-person">PER PERSON DEAL</h2>
  <p class="note">&#9656; A MINIMUM OF 10 PEOPLE ARE NEEDED FOR THE PER PERSON DEALS</p>

  <div class="option" style="left:150px"></div>
  <div class="option" style="left:309px"></div>
  <div class="option" style="left:465px"></div>

  <span class="option-label" style="left:177px">OPTION 1</span>
  <span class="option-name" style="left:177px">SNACK</span>
  <p class="option-items" style="left:177px">2 Tenders<br>Sauce<br>Dressing<br>1 Reg Side</p>
  <span class="option-price" style="left:177px">$7.00/PERSON</span>

  <span class="option-label" style="left:336px">OPTION 2</span>
  <span class="option-name" style="left:336px">PARTY</span>
  <p class="option-items" style="left:336px">2 Tenders<br>3 Wings<br>Sauce<br>Dressing<br>1 Reg Side<br>12oz Drink</p>
  <span class="option-price" style="left:336px">$11.00/PERSON</span>

  <span class="option-label" style="left:491px">OPTION 3</span>
  <span class="option-name" style="left:491px">FEAST</span>
  <p class="option-items" style="left:491px">2 Tenders<br>6 Wings<br>Sauce<br>Dressing<br>1 Reg Side<br>20oz Drink</p>
  <span class="option-price" style="left:491px">$15.00/PERSON</span>

  <h2 class="section-head head-package">PACKAGE DEALS</h2>

  <div class="package" style="left:671px">
    <div class="package-head">FAMILY</div>
    <p class="package-items" style="top:93px">12 TENDERS<br>SAUCES<br>DRESSING<br>LARGE SIDE<br>2L</p>
    <span class="package-price">$24.99</span>
  </div>
  <div class="package" style="left:813px">
    <div class="package-head">TAILGATE</div>
    <p class="package-items" style="top:76px">20 TENDERS<br>30 WINGS<br>SAUCES<br>2 PARTY SIDES<br>2 PARTY SALADS<br>DRESSINGS<br>2 2L</p>
    <span class="package-price" style="top:180px">$75.99</span>
  </div>
  <div class="package" style="left:954px">
    <div class="package-head">HOUSE<br>PARTY</div>
    <p class="package-items" style="top:76px">20 TENDERS<br>60 WINGS<br>SAUCES<br>2 PARTY SIDES<br>2 PARTY SALADS<br>DRESSINGS<br>2 2L</p>
    <span class="package-price">$155.99</span>
  </div>

  <h2 class="section-head head-own">MAKE YOUR OWN DEAL</h2>

  <div class="count-box" style="left:132px;width:111px">
    <h3 style="left:28px">WINGS</h3>
    <span class="count" style="left:27px;top:30px">50<br>$7.00</span>
    <span class="count" style="left:74px;top:30px">75<br>$XX</span>
    <span class="count" style="left:27px;top:59px">100<br>$XX</span>
  </div>
  <div class="count-box" style="left:254px;width:137px">
    <h3 style="left:30px">TENDERS</h3>
    <span class="count" style="left:30px;top:30px">30<br>$7.00</span>
    <span class="count" style="left:77px;top:30px">45<br>$XX</span>
    <span class="count" style="left:30px;top:59px">60<br>$XX</span>
  </div>

  <div class="item" style="left:417px"><h3>WAFFLE<br>FRIES</h3><p>PARTY SIZE<br><span class="price">$13.99</span></p></div>
  <div class="item" style="left:537px"><h3>GARLIC<br>PARM<br>TOTS</h3><p>PARTY SIZE<br><span class="price">$13.99</span></p></div>
  <div class="item" style="left:655px"><h3>CHICKEN<br>CAESAR<br>SALAD</h3><p>PARTY SIZE<br><span class="price">$38.99</span></p></div>
  <div class="item" style="left:778px"><h3>CAESAR<br>SALAD</h3><p>PARTY SIZE<br><span class="price">$27.99</span></p></div>
  <div class="item" style="left:898px"><h3>ANY<br>SAUCE</h3><p>8OZ<br><span class="price">$1.99</span></p></div>
  <div class="item" style="left:998px"><h3>CHEESE<br>SAUCE</h3><p>8OZ<br><span class="price">$2.49</span></p></div>

  <p class="learn-more">LEARN MORE AT <b>CRISPHARBOR-EATS.EXAMPLE/MENU</b></p>
  <svg class="cursor" width="30" height="36" viewBox="0 0 30 36" aria-hidden="true">
    <path d="M9 9 L9 30 L14 25 L18 33 L21 31 L17 24 L24 24 Z" fill="var(--white)" stroke="var(--red)" stroke-width="2" stroke-linejoin="round"/>
    <path d="M4 2 L6 6 M11 0 L11 4 M1 8 L5 8" stroke="var(--red)" stroke-width="2" stroke-linecap="round"/>
  </svg>
</div>
</body>
</html>
```